Business Cards for new orthopaedic surgery practice

My husband and I are starting our own orthopaedic surgery practice. We are looking for a business card that is uniform, but one will have my name/title and the other will have his. You can just create one design with my name on it for now. But when I choose your design as the winning design I will ask that you add another copy with his name/title.

We are looking for classy, simple, elite all in one. We like dark blues/a little gold/yellow. Something that goes with our logo. We want our logo incorporated. Here is all the info you need:
Business name: RV Bone & Vitality Center
Location: 38517 North Willowmere Ave
Coral Springs, FL 33071
Phone: 954-218-4063
Fax: 954-582-7341
Email: info@myrvbonecare.example

Names: Lydia Vance, M.D.
Board Certified Hand and Upper Extremity Surgeon

Ebo Dansu, M.D.
Board Certified Hip & Knee Replacement/General Orthopaedic Surgeon

Can decide what you want to put on the back. Maybe a slogan:
Steady Hands. Trusted Healing

I am just going to upload our logo. The only thing is if we select you as the winning design, the location, and phone numbers may change. We will need your help to update that once fully solidified.

Industry/Entity Type

Medical

Contact Information for Business Card

Colors
0054AA
0677BA
7BADD7
CADEEF
E8F1F8
0094D4
00A9DD
6FCCEA
C7EBF8
E9F6FB

Requirements
Must have
• class, appeal,
Should not have
• We want to air on the side of masculine if we are looking at masculine vs. feminine feel. But we still want it classy, sophisticated, and something we will love

```html
<!DOCTYPE html>
<html lang="en">
<head>
<meta charset="utf-8">
<title>RV Bone &amp; Vitality Center – Business Card</title>
<link rel="stylesheet" href="https://fonts.googleapis.com/css2?family=Cinzel:wght@400;600&family=Roboto:wght@400&display=swap">
<style>
  :root {
    --navy: #1c2b8c;
    --navy-deep: #17247a;
    --cyan: #1ea6d9;
    --ink: #333640;
    --paper: #f4f4f3;
    --backdrop: #e6e7e9;
  }
  * { box-sizing: border-box; margin: 0; padding: 0; }
  html, body { width: 1200px; height: 884px; overflow: hidden; background: var(--backdrop); }
  .canvas {
    width: 1200px; height: 884px;
    display: flex; flex-direction: column; align-items: center; justify-content: center; gap: 40px;
  }
  .card {
    width: 630px; height: 360px; position: relative; overflow: hidden;
    box-shadow: 0 6px 18px rgba(0,0,0,.12);
  }
  /* Front */
  .card-front { background: var(--paper); }
  .brand {
    position: absolute; left: 40px; top: 100px; width: 250px;
    display: flex; flex-direction: column; align-items: center; gap: 14px;
  }
  .brand-mark { width: 34px; height: 34px; border-radius: 50%; background: var(--navy); }
  .brand-name {
    font-family: "Cinzel", serif; font-weight: 600; color: var(--navy);
    font-size: 21px; text-align: center; line-height: 1.25; letter-spacing: .5px;
  }
  .divider { position: absolute; left: 318px; top: 52px; width: 1px; height: 200px; background: var(--cyan); }
  .details { position: absolute; left: 340px; top: 44px; right: 20px; }
  .person-name {
    font-family: "Cinzel", serif; font-weight: 600; color: var(--navy);
    font-size: 19px; letter-spacing: .3px;
  }
  .person-title { font-family: "Roboto", sans-serif; color: var(--cyan); font-size: 15px; line-height: 1.25; margin-top: 3px; }
  .contact { list-style: none; margin-top: 18px; font-family: "Roboto", sans-serif; color: var(--ink); font-size: 14px; }
  .contact li { display: flex; align-items: flex-start; gap: 8px; line-height: 1.3; }
  .contact li.address { margin-bottom: 10px; }
  .contact svg { width: 14px; height: 14px; flex: none; margin-top: 2px; fill: var(--navy); }
  .slogan-band {
    position: absolute; left: 0; right: 0; bottom: 0; height: 34px; background: var(--navy);
    display: flex; align-items: center; justify-content: center;
    font-family: "Cinzel", serif; font-size: 12px; letter-spacing: 3px; color: var(--cyan);
  }
  /* Back */
  .card-back { background: var(--navy); }
  .monogram-field {
    position: absolute; inset: 0;
    background: radial-gradient(ellipse at 30% 40%, #6e7aa8 0%, #2a3890 45%, var(--navy-deep) 100%);
  }
  .back-brand {
    position: absolute; left: 0; right: 0; top: 150px;
    display: flex; align-items: center; justify-content: center; gap: 12px;
  }
  .back-brand .brand-mark { background: #ffffff; width: 28px; height: 28px; }
  .back-brand .brand-name { color: #ffffff; font-size: 24px; }
</style>
</head>
<body>
<main class="canvas">
  <section class="card card-front">
    <div class="brand">
      <span class="brand-mark"></span>
      <p class="brand-name">RV Bone &amp; Vitality<br>Center</p>
    </div>
    <div class="divider"></div>
    <div class="details">
      <h1 class="person-name">LYDIA VANCE, M.D.</h1>
      <p class="person-title">Board Certified Hand and<br>Upper Extremity Surgeon</p>
      <ul class="contact">
        <li class="address">
          <svg viewBox="0 0 24 24"><path d="M12 2a7 7 0 0 0-7 7c0 5 7 13 7 13s7-8 7-13a7 7 0 0 0-7-7zm0 9.5A2.5 2.5 0 1 1 12 6.5a2.5 2.5 0 0 1 0 5z"/></svg>
          <span>38517 North Willowmere Ave<br>Coral Springs, FL 33071</span>
        </li>
        <li>
          <svg viewBox="0 0 24 24"><path d="M6.6 10.8a15 15 0 0 0 6.6 6.6l2.2-2.2a1 1 0 0 1 1-.25 11.4 11.4 0 0 0 3.6.57 1 1 0 0 1 1 1V20a1 1 0 0 1-1 1A17 17 0 0 1 3 4a1 1 0 0 1 1-1h3.5a1 1 0 0 1 1 1c0 1.25.2 2.45.57 3.6a1 1 0 0 1-.25 1z"/></svg>
          <span>954-218-4063</span>
        </li>
        <li>
          <svg viewBox="0 0 24 24"><path d="M7 3h8l3 3v4h1a2 2 0 0 1 2 2v7a2 2 0 0 1-2 2H5a2 2 0 0 1-2-2v-7a2 2 0 0 1 2-2h2zm2 2v5h7V7h-2V5zm-2 9v2h10v-2z"/></svg>
          <span>954-582-7341</span>
        </li>
        <li>
          <svg viewBox="0 0 24 24"><path d="M3 5h18v14H3zm2 2v.5l7 5 7-5V7zm0 3v7h14v-7l-7 5z"/></svg>
          <span>info@myrvbonecare.example</span>
        </li>
        <li>
          <svg viewBox="0 0 24 24"><path d="M12 2a10 10 0 1 0 0 20 10 10 0 0 0 0-20zm6.9 6h-3a15 15 0 0 0-1.3-4 8 8 0 0 1 4.3 4zM12 4c.9 1.2 1.6 2.6 2 4h-4c.4-1.4 1.1-2.8 2-4zM4.3 14a8 8 0 0 1 0-4h3.4a16 16 0 0 0 0 4zm.8 2h3a15 15 0 0 0 1.3 4 8 8 0 0 1-4.3-4zm3-8h-3a8 8 0 0 1 4.3-4 15 15 0 0 0-1.3 4zM12 20c-.9-1.2-1.6-2.6-2-4h4c-.4 1.4-1.1 2.8-2 4zm2.3-6H9.7a14 14 0 0 1 0-4h4.6a14 14 0 0 1 0 4zm.3 6a15 15 0 0 0 1.3-4h3a8 8 0 0 1-4.3 4zm1.7-6a16 16 0 0 0 0-4h3.4a8 8 0 0 1 0 4z"/></svg>
          <span>www.lydiavancehand.example</span>
        </li>
      </ul>
    </div>
    <div class="slogan-band">STEADY HANDS. TRUSTED HEALING</div>
  </section>

  <section class="card card-back">
    <div class="monogram-field" role="img" aria-label="Embossed repeating pattern of the practice monogram in silver and navy"></div>
    <div class="back-brand">
      <span class="brand-mark"></span>
      <p class="brand-name">RV Bone &amp; Vitality Center</p>
    </div>
  </section>
</main>
</body>
</html>
```